Dental Implant Logo and Business Card for Local Dentist

Design a unique business card and a logo that incorporates a dental implant as a primary focal point or a part of the text. New logo design & business card needs to incorporate our businesses old star shaped logo (attached) and a dental implant, along with our business name. Star logo does not have to remain the exact same colors and can be any size. Looking for a warm, friendly (non-aggressive) design that uses colors in the blue-green palate, partial to mint-turquoise color similar to the images attached . SIMPLE IS GOOD, but looking for creativity to bring all the elements together. OK to incorporate a splash of color. I have attached a few images of implant logos I like along with our existing star shaped logo. *I have also uploaded some images that represent local landscapes & images for the back of the business card. I would like to include a silhouette or sketch that represents one one of these areas on the back of the business card to convey the connection to our community and local roots of our business since we are 4th generation members of this community . Can visit our dental practice website for more info. www.hartwellandodegarddentalcare.example Card Must Haves on Front of Card:1. business name "Hartwell & Odegard Dental Care" 2. My Name: "Colin Odegard D.D.S."3. Phone # (925) 754-6020Other info for card (can be front or back)Address: 7840 Quarry Ridge Rd. #2C Antioch, Ca 94531e-mail: millerandsimarrodentalcare@gmail.comcosmetic, family, & impDesign a unique business card and a logo that incorporates a dental implant as a primary focal point or a part of the text. New logo design & business card needs to incorporate our businesses old star shaped logo (attached) and a dental implant, along with our business name. Star logo does not have to remain the exact same colors and can be any size. Looking for a warm, friendly (non-aggressive) design that uses colors in the blue-green palate, partial to mint-turquoise color similar to the images attached . SIMPLE IS GOOD, but looking for creativity to bring all the elements together. OK to incorporate a splash of color. I have attached a few images of implant logos I like along with our existing star shaped logo. *I have also uploaded some images that represent local landscapes & images for the back of the business card. I would like to include a silhouette or sketch that represents one one of these areas on the back of the business card to convey the connection to our community and local roots of our business since we are 4th generation members of this community . Can visit our dental practice website for more info. www.hartwellandodegarddentalcare.example Card Must Haves on Front of Card:1. business name "Hartwell & Odegard Dental Care" 2. My Name: "Colin Odegard D.D.S."3. Phone # (925) 754-6020Other info for card (can be front or back)Address: 7840 Quarry Ridge Rd. #2C Antioch, Ca 94531e-mail: millerandsimarrodentalcare@gmail.comcosmetic, family, & implant dentistry

Target Market(s)

Families

Industry/Entity Type

Dental

Contact Information for Business Card

See Project description above

Logo Text

Hartwell & Odegard Dental Care

Font styles to use
Serif

Colors
ffffff
33b8a4
87cfc6
0492cd
33a6d7
0255a3

Requirements
Must have
• *See Description...
• Card Must Haves on Front of Card:
• 1. business name "Hartwell & Odegard Dental Care"
• 2. My Name: "Colin Odegard D.D.S."
• 3. Phone # (555) 318-4297
• Other info for card (can be front or back)
• Address: 7840 Quarry Ridge Rd. #2C Antioch, Ca 90217
• e-mail: hartwellandodegarddentalcare@example-mail.com
Nice to have
• Local image sketch or silhouette on back side of business card with remaining information on back: address, website, e-mail etc.

```html
<!DOCTYPE html>
<html lang="en">
<head>
<meta charset="utf-8">
<title>Hartwell &amp; Odegard Dental Care – Business Card</title>
<link rel="stylesheet" href="https://fonts.googleapis.com/css2?family=Tenor+Sans&family=Barlow:wght@400;500;600&family=Noto+Serif:wght@400&display=swap">
<style>
  :root {
    --bg: #e9e4da;
    --card-green: #45563a;
    --white: #ffffff;
    --tagline: #e6e8e0;
    --accent-orange: #d9912f;
    --divider-green: #7cbf3a;
    --sky-top: #3f64a4;
    --sky-low: #6f9fcf;
    --hill: #c9a65a;
    --water: #6f8e94;
    --back-blue: #0255a3;
    --back-teal: #33b8a4;
  }
  * { box-sizing: border-box; margin: 0; padding: 0; }
  html, body { width: 1200px; height: 1200px; overflow: hidden; }
  body {
    background: var(--bg);
    display: flex; flex-direction: column; align-items: center; justify-content: center;
    gap: 40px;
  }
  .card {
    width: 960px; height: 548px; position: relative; overflow: hidden;
    box-shadow: 0 6px 18px rgba(0,0,0,.18);
  }
  /* Front */
  .card-front { background: var(--card-green); color: var(--white); }
  .brand {
    position: absolute; left: 50px; right: 50px; top: 72px;
    display: flex; align-items: center; gap: 20px;
  }
  .brand-mark { width: 72px; height: 72px; border-radius: 50%; background: var(--accent-orange); flex: none; }
  .brand-text { min-width: 0; }
  .brand-name {
    font-family: "Tenor Sans", sans-serif; font-size: 47px; line-height: 1; color: var(--white);
    white-space: nowrap;
  }
  .brand-tagline {
    font-family: "Tenor Sans", sans-serif; font-size: 16px; letter-spacing: 12px;
    color: var(--tagline); margin-top: 8px; white-space: nowrap;
  }
  .person {
    position: absolute; right: 560px; top: 250px; text-align: right;
    font-family: "Barlow", sans-serif;
  }
  .person-name { font-size: 28px; font-weight: 600; letter-spacing: .5px; }
  .person-role { font-size: 19px; color: var(--accent-orange); margin-top: 2px; }
  .divider {
    position: absolute; left: 418px; top: 250px; width: 2px; height: 88px;
    background: var(--divider-green);
  }
  .contact {
    position: absolute; left: 440px; top: 246px; list-style: none;
    font-family: "Barlow", sans-serif; font-size: 19px; letter-spacing: .3px;
  }
  .contact li { display: flex; align-items: center; gap: 12px; height: 31px; white-space: nowrap; }
  .contact svg { width: 17px; height: 17px; flex: none; }
  .address {
    position: absolute; left: 0; right: 0; top: 440px; text-align: center;
    font-family: "Barlow", sans-serif; font-size: 23px; font-weight: 500; letter-spacing: .4px;
  }
  /* Back */
  .card-back { background: linear-gradient(180deg, var(--sky-top) 0%, var(--sky-low) 48%, var(--hill) 60%, var(--hill) 70%, var(--water) 78%, var(--water) 100%); }
  .back-scene { position: absolute; inset: 0; }
  .back-brand {
    position: absolute; right: 60px; bottom: 46px; text-align: right;
  }
  .back-name { font-family: "Noto Serif", serif; font-size: 36px; color: var(--back-blue); }
  .back-tagline {
    font-family: "Noto Serif", serif; font-size: 13px; letter-spacing: 8px; color: var(--back-teal); margin-top: 2px;
  }
</style>
</head>
<body>
  <section class="card card-front">
    <div class="brand">
      <span class="brand-mark"></span>
      <div class="brand-text">
        <div class="brand-name">Hartwell &amp; Odegard Dental Care</div>
        <div class="brand-tagline">COSMETIC &amp; GENERAL DENTISTRY</div>
      </div>
    </div>

    <div class="person">
      <div class="person-name">Colin Odegard D.D.S</div>
      <div class="person-role">manager</div>
    </div>
    <div class="divider"></div>

    <ul class="contact">
      <li>
        <svg viewBox="0 0 24 24" aria-hidden="true"><path fill="#d9912f" d="M6.6 10.8a15.1 15.1 0 0 0 6.6 6.6l2.2-2.2c.3-.3.7-.4 1-.2 1.1.4 2.3.6 3.6.6.6 0 1 .4 1 1V20c0 .6-.4 1-1 1A17 17 0 0 1 3 4c0-.6.4-1 1-1h3.5c.6 0 1 .4 1 1 0 1.3.2 2.5.6 3.6.1.3 0 .7-.2 1z"/></svg>
        <span>+(555) - 318-4297</span>
      </li>
      <li>
        <svg viewBox="0 0 24 24" aria-hidden="true"><rect x="2" y="5" width="20" height="14" rx="1" fill="#d9912f"/><path d="M3 6l9 7 9-7" fill="none" stroke="#45563a" stroke-width="1.8"/></svg>
        <span>hartwellandodegarddentalcare@example-mail.com</span>
      </li>
      <li>
        <svg viewBox="0 0 24 24" aria-hidden="true"><g fill="none" stroke="#d9912f" stroke-width="2"><circle cx="12" cy="12" r="9"/><ellipse cx="12" cy="12" rx="4" ry="9"/><path d="M3 12h18"/></g></svg>
        <span>www.hartwellandodegarddentalcare.example</span>
      </li>
    </ul>

    <div class="address">7840 Quarry Ridge Rd. #2C Antioch, Ca 90217</div>
  </section>

  <section class="card card-back">
    <div class="back-scene" role="img" aria-label="Photograph of wind turbines on golden hills above a river with a windsurfer sailing"></div>
    <div class="back-brand">
      <div class="back-name">Hartwell &amp; Odegard Dental Care</div>
      <div class="back-tagline">COSMETIC &amp; GENERAL DENTISTRY</div>
    </div>
  </section>
</body>
</html>
```